Locksmith Business Cards

My father-in-law is in need of new business cards for his locksmith business and I need to impress him. Kindly help me out!

You can see the previous business card attached. It is a family run business in North Wales.

No individual names on the cards.

Key Things to Feature:
- The words "Prompt", "Local", "Reliable" (as you can see under the logo on the website)
- 24h Emergency Service
- Covering All of North Wales, the Wirral and Chester
- The color blue
- A key or a lock would be interesting (similar to the ones that come up when you google locksmith business card)

Optional (only if design includes bullet points, like the example below):
https://imgvaultcdn.net/samples/208314/55172/55172_3904821_208314_image.jpg
- Residential / Commercial / Automotive
- Alarms & Cameras
- Key Cutting & Safes

https://www.brynhafod-locksmiths.co.uk/

Industry/Entity Type

Locksmith

Contact Information for Business Card

01632 960 418
07700 900 362
brynhafodlocksmiths@mailvane.com
Brynhafod Locksmiths, The Willow Barn, 7 Tannery Rd., Llandudno LL99 4QX
www.brynhafod-locksmiths.co.uk

Requirements
Must have
• - The words "Prompt", "Local", "Reliable" (as you can see under the logo on the website)
• - 24h Emergency Service
• - Covering All of North Wales, the Wirral and Chester
Nice to have
• - A key or a lock would be interesting (similar to the ones that come up when you google locksmith business card)

```html
<!DOCTYPE html>
<html lang="en">
<head>
<meta charset="utf-8">
<title>Brynhafod Locksmiths – Business Card</title>
<link href="https://fonts.googleapis.com/css2?family=Roboto+Condensed:wght@400;700&family=Roboto:wght@400;500&display=swap" rel="stylesheet">
<style>
  :root {
    --navy: #242a66;
    --blue: #4b5cab;
    --pale-blue: #a3addb;
    --white: #ffffff;
    --ink: #1f2452;
    --stage: #e6e7ec;
  }
  * { box-sizing: border-box; margin: 0; padding: 0; }
  html, body { width: 1200px; height: 900px; overflow: hidden; }
  body {
    background: var(--stage);
    font-family: "Roboto", Arial, sans-serif;
    color: var(--ink);
    display: flex;
    flex-direction: column;
    align-items: center;
    justify-content: center;
    gap: 40px;
  }
  .card {
    position: relative;
    width: 700px;
    height: 400px;
    border-radius: 22px;
    overflow: hidden;
    box-shadow: 0 8px 24px rgba(20, 24, 60, .18);
  }

  /* Front */
  .card-front { background: var(--white); }
  .brand { position: absolute; left: 44px; top: 38px; display: flex; align-items: center; gap: 14px; }
  .brand-mark { width: 54px; height: 54px; background: var(--navy); border-radius: 8px; }
  .brand-name {
    font-family: "Roboto Condensed", "Arial Narrow", sans-serif;
    font-weight: 700; font-size: 34px; line-height: 1; letter-spacing: .5px;
    color: var(--navy); text-transform: uppercase;
  }
  .tagline {
    position: absolute; left: 112px; top: 100px;
    font-size: 19px; color: var(--navy); letter-spacing: .3px;
  }
  .divider { position: absolute; left: 40px; right: 40px; top: 160px; height: 1.5px; background: var(--pale-blue); }
  .contacts { position: absolute; left: 40px; top: 186px; list-style: none; font-size: 16px; line-height: 26px; }
  .contacts li { display: flex; align-items: center; gap: 10px; }
  .contacts svg { width: 14px; height: 14px; fill: var(--blue); flex: none; }
  .office { position: absolute; right: 44px; top: 186px; text-align: right; }
  .office-title {
    font-family: "Roboto Condensed", "Arial Narrow", sans-serif;
    font-weight: 700; font-size: 24px; letter-spacing: 1px; color: var(--blue);
  }
  .office-rule { height: 1.5px; background: var(--pale-blue); width: 260px; margin: 8px 0 8px auto; }
  .address { font-size: 15px; line-height: 21px; font-style: normal; }
  .address .company { color: var(--blue); }
  .front-band { position: absolute; left: 0; bottom: 0; width: 700px; height: 70px; }

  /* Back */
  .card-back { background: var(--navy); color: var(--white); padding: 38px 56px; }
  .card-back .brand { position: static; }
  .card-back .brand-mark { background: var(--white); }
  .card-back .brand-name { color: var(--white); font-size: 40px; }
  .service { font-size: 30px; line-height: 36px; margin: 20px 0 12px; font-family: "Roboto Condensed", "Arial Narrow", sans-serif; }
  .services { list-style: none; font-size: 23px; line-height: 32px; font-weight: 500; }
  .services li { display: flex; align-items: center; gap: 16px; }
  .services li::before { content: ""; width: 11px; height: 11px; border-radius: 50%; background: var(--white); }
  .coverage { margin-top: 14px; font-size: 18px; line-height: 24px; color: var(--pale-blue); }
</style>
</head>
<body>

<section class="card card-front" aria-label="Business card front">
  <div class="brand">
    <span class="brand-mark"></span>
    <span class="brand-name">Brynhafod Locksmiths</span>
  </div>
  <p class="tagline">Prompt. Local. Reliable</p>
  <div class="divider"></div>

  <ul class="contacts">
    <li><svg viewBox="0 0 24 24"><path d="M6.6 10.8a15 15 0 0 0 6.6 6.6l2.2-2.2a1 1 0 0 1 1-.25 11.4 11.4 0 0 0 3.6.57 1 1 0 0 1 1 1V20a1 1 0 0 1-1 1A17 17 0 0 1 3 4a1 1 0 0 1 1-1h3.5a1 1 0 0 1 1 1c0 1.25.2 2.45.57 3.57a1 1 0 0 1-.25 1z"/></svg>01632 960 418</li>
    <li><svg viewBox="0 0 24 24"><path d="M7 1h10a2 2 0 0 1 2 2v18a2 2 0 0 1-2 2H7a2 2 0 0 1-2-2V3a2 2 0 0 1 2-2zm0 3v14h10V4z"/></svg>07700 900 362</li>
    <li><svg viewBox="0 0 24 24"><path d="M2 5h20v14H2zm2 2v.5l8 5 8-5V7zm0 2.8V17h16V9.8l-8 5z"/></svg>brynhafodlocksmiths@mailvane.com</li>
    <li><svg viewBox="0 0 24 24"><path d="M12 2a10 10 0 1 0 0 20 10 10 0 0 0 0-20zm7.9 9h-3.9a15 15 0 0 0-1.4-6.3A8 8 0 0 1 19.9 11zM12 4c.9 1.2 1.8 3.8 2 7h-4c.2-3.2 1.1-5.8 2-7zM9.4 4.7A15 15 0 0 0 8 11H4.1a8 8 0 0 1 5.3-6.3zM4.1 13H8a15 15 0 0 0 1.4 6.3A8 8 0 0 1 4.1 13zM12 20c-.9-1.2-1.8-3.8-2-7h4c-.2 3.2-1.1 5.8-2 7zm2.6-.7A15 15 0 0 0 16 13h3.9a8 8 0 0 1-5.3 6.3z"/></svg>www.brynhafod-locksmiths.co.uk</li>
  </ul>

  <div class="office">
    <p class="office-title">24H EMERGENCY SERVICE</p>
    <div class="office-rule"></div>
    <address class="address">
      <span class="company">Brynhafod Locksmiths,</span><br>
      The Willow Barn, 7 Tannery Rd.,<br>
      Llandudno LL99 4QX
    </address>
  </div>

  <svg class="front-band" viewBox="0 0 700 70" preserveAspectRatio="none" aria-hidden="true">
    <polygon points="0,38 280,38 280,70 0,70" fill="var(--blue)"/>
    <polygon points="270,70 292,30 700,30 700,70" fill="var(--navy)"/>
  </svg>
</section>

<section class="card card-back" aria-label="Business card back">
  <div class="brand">
    <span class="brand-mark"></span>
    <span class="brand-name">Brynhafod Locksmiths</span>
  </div>
  <p class="service">24h Emergency Service</p>
  <ul class="services">
    <li>Residential</li>
    <li>Commercial</li>
    <li>Automotive</li>
    <li>Alarms &amp; Cameras</li>
    <li>Key Cutting &amp; Safes</li>
  </ul>
  <p class="coverage">Covering All of North Wales, the Wirral and Chester</p>
</section>

</body>
</html>
```